Presentation Folder, for Cancer Awareness, VERY COLORFULL AND MODERN

This will be a standard size folder that will hold standard 8 1/2 x 11 papers with a business card slot on the flap, this is a very easy project with very little text and the design for the back page is already done so all you really have to do is make a very nice colorful front cover, you will see my attachments are labeled and I gave you alot of instructions, this should be a very fast easy project
Updates

Reason: there has not been enough quality designs, sorry

Target Market(s)

Our Target Market is Dr's that Deal with Cancer patients

Industry/Entity Type

Healthcare

Font styles to use
Serif

Colors

Designer to choose colors to be used in the design.

Requirements
Must have
• Project must be tasteful and look professional with the ribbons as the main focal point in the center of folder the folder should be a nice gray color to accent the color of the ribbons , the back page needs no design it is the" Sorvane Test" in the attachments I sent
Nice to have
• I would like the ribbons displayed in a row, I included a logo sample layout
• a picture on the front of the folder under the words Hereditary Cancer Screening - Then under that put the words - The Power of Knowledge - then add the picture I labeled Great Picture in the attachments

```html
<!DOCTYPE html>
<html lang="en">
<head>
<meta charset="utf-8">
<title>Hereditary Cancer Screening Folder</title>
<link href="https://fonts.googleapis.com/css2?family=Josefin+Sans:ital,wght@0,300;0,400;0,600;0,700;1,700&family=Raleway:wght@300;400;500;600&display=swap" rel="stylesheet">
<style>
:root{
  --red:#e8202a;
  --cut:#e5343a;
  --pink:#ee6fd6;
  --navy:#1c2466;
  --ink:#222;
  --folder:#e6e6e8;
  --sheet:#ffffff;
  --grey-row:#ebebeb;
  --strip:#c6c6c8;
  --lynch:#fbbf2a;
  --peutz:#a4e02c;
  --lifr:#4fe42c;
  --cowden:#13cff5;
  --diffuse:#3d3d3b;
  --muted:#666;
}
*{box-sizing:border-box;margin:0;padding:0}
html,body{width:1200px;height:960px;overflow:hidden;background:#fff}
body{font-family:"Josefin Sans",sans-serif;color:var(--ink)}
.folder{position:relative;width:1200px;height:960px}
.dieline{position:absolute;inset:0}
.abs{position:absolute}

/* back panel */
.brand-name{left:110px;top:55px;font-size:15px;letter-spacing:5px;color:var(--red);font-weight:400}
.contact{left:110px;top:78px;font-size:5.2px;line-height:7px;letter-spacing:.4px;color:#555;font-family:"Raleway",sans-serif}
.menu-title{left:369px;top:54px;font-size:16px;font-weight:700;font-style:italic;color:var(--red)}
.menu-title sup{font-size:6px}
.menu-id{left:408px;top:86px;font-size:5.2px;color:#555;letter-spacing:.4px;font-family:"Raleway",sans-serif}

.gene-table{left:128px;top:101px;width:422px;border-collapse:collapse;background:var(--sheet)}
.gene-table td{height:14.6px;padding:0;font-size:7.6px;vertical-align:middle;white-space:nowrap}
.gene-table td.gene{width:140px;padding-left:8px;color:var(--red);font-weight:700;letter-spacing:1px}
.gene-table td.organ{font-family:"Raleway",sans-serif;color:#222;letter-spacing:.2px}
.gene-table tr.alt td{background:var(--grey-row)}
.gene-table tr.sub td.gene{padding-left:19px}
.gene-table tr.head td{background:var(--red);color:#fff;font-weight:400;letter-spacing:1.3px;font-size:9px}
.gene-table tr.band td{color:#fff;letter-spacing:1.2px;font-size:8.6px;padding-left:19px}
.band.lynch td{background:var(--lynch)}
.band.peutz td{background:var(--peutz)}
.band.lifr td{background:var(--lifr)}
.band.cowden td{background:var(--cowden)}
.band.diffuse td{background:var(--diffuse)}

.partner{left:94px;top:906px;font-size:19.5px;font-weight:600;color:#111;font-family:"Raleway",sans-serif}
.partner-note{left:314px;top:914px;font-size:11px;color:#555;font-family:"Raleway",sans-serif}

/* front cover */
.cover-title{left:596px;width:540px;text-align:center;top:93px;font-size:26.5px;font-weight:700;color:var(--pink);letter-spacing:1px;white-space:nowrap}
.cover-sub{left:596px;width:540px;text-align:center;top:124px;font-size:27px;font-weight:400;color:var(--navy);letter-spacing:1.2px;white-space:nowrap}
.photo{left:645px;top:220px;width:508px;height:320px;transform:rotate(-4deg);
  background:linear-gradient(135deg,#d9cbb6 0%,#b99e83 40%,#8e8c8e 70%,#c9c3bb 100%);
  box-shadow:4px 6px 10px rgba(0,0,0,.35);border:3px solid #fff}
.ribbon{left:1122px;top:102px;width:40px;height:138px}
.logo-mark{left:712px;top:601px;width:32px;height:32px;border-radius:50%;background:var(--red)}
.logo-name{left:622px;top:640px;width:152px;text-align:center;font-size:15px;letter-spacing:5px;color:var(--red)}
.cancer-list{left:780px;width:390px;top:620px;text-align:center;font-size:13px;line-height:16px;color:var(--muted);font-family:"Raleway",sans-serif;font-weight:300;white-space:nowrap}
.facility{left:640px;width:464px;top:761px;text-align:center;font-size:13px;line-height:16.3px;color:#333;font-family:"Raleway",sans-serif;font-weight:300;white-space:nowrap}
.facility p+p{margin-top:16px}
</style>
</head>
<body>
<div class="folder">
  <svg class="dieline" width="1200" height="960" viewBox="0 0 1500 1200" aria-hidden="true">
    <path fill="var(--folder)" d="M0,40 Q0,20 20,20 L1480,20 Q1500,20 1500,40 L1500,530 A28,28 0 0 0 1500,586 L1500,862 L1440,880 L1440,1200 L60,1200 L60,880 L0,862 L0,586 A28,28 0 0 0 0,530 Z"/>
    <rect x="60" y="880" width="45" height="320" fill="var(--strip)"/>
    <rect x="1395" y="880" width="45" height="320" fill="var(--strip)"/>
    <g fill="none" stroke="var(--cut)" stroke-width="1.4">
      <path d="M0,40 Q0,20 20,20 L1480,20 Q1500,20 1500,40 L1500,530 A28,28 0 0 0 1500,586 L1500,862 L1440,880 L1440,1200"/>
      <path d="M0,40 L0,530 A28,28 0 0 1 0,586 L0,862 L60,880 L60,1200"/>
      <path d="M655,1200 Q697,1200 700,1160 L744,885 Q750,872 756,885 L800,1160 Q803,1200 845,1200"/>
      <path d="M270,1007 L315,963 M487,963 L531,1007 M270,1071 L315,1115 M487,1115 L531,1071"/>
    </g>
  </svg>

  <!-- back panel -->
  <div class="abs brand-name">GENVISTA</div>
  <div class="abs contact">820 LARKWOOD AVENUE | SUITE B | FAIRHAVEN, GA 30412<br>(tel) 555.014.2231 | (fax) 555.014.2290 | care@genvista.example</div>
  <div class="abs menu-title">SORVANE<sup>™</sup> Test Menu</div>
  <div class="abs menu-id">CLIA# 00X0000000 &nbsp;|&nbsp; GENVISTA.EXAMPLE</div>

  <table class="abs gene-table">
    <tr class="head"><td class="gene">GENE</td><td>CANCER-ASSOCIATED ORGAN/SYSTEMS</td></tr>
    <tr><td class="gene">APC</td><td class="organ">Colon</td></tr>
    <tr class="alt"><td class="gene">ATM</td><td class="organ">Breast/Pancreatic/Brain</td></tr>
    <tr><td class="gene">BARD1</td><td class="organ">Breast/Ovarian</td></tr>
    <tr class="alt"><td class="gene">BMPR1A</td><td class="organ">Colon</td></tr>
    <tr><td class="gene">BRCA1</td><td class="organ">Breast/Ovarian/Prostate</td></tr>
    <tr class="alt"><td class="gene">BRCA2</td><td class="organ">Breast/Ovarian/Prostate</td></tr>
    <tr><td class="gene">BRIP1</td><td class="organ">Breast/Ovarian</td></tr>
    <tr class="alt"><td class="gene">CDK4</td><td class="organ">Melanoma</td></tr>
    <tr><td class="gene">P16 (CDKN2A)</td><td class="organ">Melanoma/Breast/Pancreatic/Squamous</td></tr>
    <tr class="alt"><td class="gene">FANCC</td><td class="organ">Blood</td></tr>
    <tr><td class="gene">MEN1</td><td class="organ">Thyroid/Parathyroid</td></tr>
    <tr class="alt"><td class="gene">MET</td><td class="organ">Renal/Hepatic</td></tr>
    <tr><td class="gene">MRE11A</td><td class="organ">Ovarian/Breast</td></tr>
    <tr class="alt"><td class="gene">NBN</td><td class="organ">Breast/Ovarian/Prostate/Melanoma</td></tr>
    <tr><td class="gene">NF1</td><td class="organ">Blood</td></tr>
    <tr class="alt"><td class="gene">NTRK1</td><td class="organ">Thyroid/Parathyroid</td></tr>
    <tr><td class="gene">PALB2</td><td class="organ">Breast/Ovarian/Pancreatic</td></tr>
    <tr class="alt"><td class="gene">PTCH1</td><td class="organ">Melanoma/Brain/Breast/Colon</td></tr>
    <tr><td class="gene">RAD50</td><td class="organ">Breast/Ovarian</td></tr>
    <tr class="alt"><td class="gene">RAD51C</td><td class="organ">Ovarian/Breast</td></tr>
    <tr><td class="gene">RAD51D</td><td class="organ">Ovarian/Breast</td></tr>
    <tr class="alt"><td class="gene">RET</td><td class="organ">Lung/Thyroid/Parathyroid</td></tr>
    <tr><td class="gene">SMAD4</td><td class="organ">Colon/Pancreas</td></tr>
    <tr class="band lynch"><td colspan="2">LYNCH SYNDROME GENES</td></tr>
    <tr class="sub"><td class="gene">MLH1</td><td class="organ">Colorectal/Ovarian</td></tr>
    <tr class="sub alt"><td class="gene">MSH2</td><td class="organ">Colorectal/Ovarian</td></tr>
    <tr class="sub"><td class="gene">MSH6</td><td class="organ">Colorectal/Ovarian</td></tr>
    <tr class="sub alt"><td class="gene">PMS2</td><td class="organ">Colorectal/Ovarian</td></tr>
    <tr class="sub"><td class="gene">EPCAM</td><td class="organ">Colorectal</td></tr>
    <tr class="band peutz"><td colspan="2">PEUTZ-JEGHERS SYNDROME GENE</td></tr>
    <tr class="sub"><td class="gene">STK11</td><td class="organ">Breast/Ovarian/Melanoma/Colorectal/Lung</td></tr>
    <tr class="band lifr"><td colspan="2">LI-FRAUMENI SYNDROME GENE</td></tr>
    <tr class="sub"><td class="gene">CHEK2</td><td class="organ">Breast/Ovarian/Prostate</td></tr>
    <tr class="sub alt"><td class="gene">PT53</td><td class="organ">Breast/Bladder/Ovarian/Squamous</td></tr>
    <tr class="band cowden"><td colspan="2">COWDEN SYNDROME GENE</td></tr>
    <tr class="sub"><td class="gene">PTEN</td><td class="organ">Endometrium/Breast/Prostate/Lung</td></tr>
    <tr class="band diffuse"><td colspan="2">HEREDITARY DIFFUSE GASTRIC CANCER SYNDROME GENE</td></tr>
    <tr class="sub alt"><td class="gene">CDH1</td><td class="organ">Breast/Gastric/Ovarian/Prostate</td></tr>
    <tr class="sub"><td class="gene">VHL</td><td class="organ">Renal</td></tr>
  </table>

  <div class="abs partner">Orrin Health Partners</div>
  <div class="abs partner-note">an independent arm of Genvista LLC</div>

  <!-- front cover -->
  <h1 class="abs cover-title">HEREDITARY CANCER SCREENING</h1>
  <h2 class="abs cover-sub">POWER OF KNOWLEDGE</h2>
  <div class="abs photo" role="img" aria-label="Photo of a multi-generation family sharing a meal at an outdoor table"></div>
  <svg class="abs ribbon" viewBox="0 0 40 138" role="img" aria-label="Awareness ribbon in lavender and light blue">
    <defs>
      <linearGradient id="ribbonTone" x1="0" y1="0" x2="1" y2="1">
        <stop offset="0" stop-color="#b58ee8"/>
        <stop offset="1" stop-color="#62d3ee"/>
      </linearGradient>
    </defs>
    <rect x="0" y="0" width="40" height="138" rx="10" fill="url(#ribbonTone)"/>
  </svg>

  <div class="abs logo-mark"></div>
  <div class="abs logo-name">GENVISTA</div>
  <div class="abs cancer-list">BREAST, OVARIAN, ENDOMETRIAL, GASTRIC, COLORECTAL,<br>PANCREATIC, MELANOMA, PROSTATE, LUNG, COLON</div>

  <div class="abs facility">
    <p>At our state of the art, CLIA certified and COLA accredited facility we<br>perform Next Generation Sequencing (NGS) based screening for<br>mutations known to affect an individual’s risk of<br>developing Hereditary Cancer.</p>
    <p>Results from the test enable the Physician to make<br>better informed treatment decisions.</p>
  </div>
</div>
</body>
</html>
```